Communication and Marketing agency needs a new presentation card

We are a group of communication and marketing agencies specialized in companies that are in the logistics and industrial sector. The head agency is TELVANO Grupo and the group consists of 4 agencies: TELVANO Media, TELVANO Digital, TELVANO Research and DifundeEnPantalla. We hace 4 offices in Spain (Madrid, Barcelona, Valencia and Murcia). We are looking for a clean and attractive design that transmits our experience, brand presence in the market and knowledge to those who receive the card.It has to maintain the colors of the logo that is attached.
Target Market(s)
logistics and industrial sector
Marketing department
Contact Information for Business Card
Clean and attractive design

```html
<!DOCTYPE html>
<html lang="es">
<head>
<meta charset="utf-8">
<title>TELVANO Grupo – Business Card</title>
<link rel="stylesheet" href="https://fonts.googleapis.com/css2?family=Roboto:wght@400;500;700&display=swap">
<style>
  :root {
    --brand-red: #b31b25;
    --ink: #1e1e1e;
    --ink-soft: #4a4a4a;
    --rule-grey: #9a9a9a;
    --paper: #ffffff;
    --backdrop: #dedede;
  }
  * { margin: 0; padding: 0; box-sizing: border-box; }
  html, body {
    width: 1125px; height: 1200px; overflow: hidden;
    background: var(--backdrop);
    font-family: "Roboto", Arial, sans-serif;
  }
  .stage { position: relative; width: 1125px; height: 1200px; }

  .card {
    position: absolute; left: 171px; width: 826px; height: 472px;
    box-shadow: 0 2px 4px rgba(0,0,0,0.18);
  }
  .card--front { top: 106px; background: var(--paper); }
  .card--back { top: 639px; background: var(--brand-red); }

  /* Front */
  .front-brand {
    position: absolute; right: 458px; top: 190px;
    text-align: right; color: var(--brand-red);
    font-weight: 500; line-height: 1;
  }
  .front-brand__name { display: block; font-size: 52px; letter-spacing: 1px; }
  .front-brand__unit { display: block; font-size: 30px; margin-top: 4px; }

  .front-divider {
    position: absolute; left: 409px; top: 129px;
    width: 1px; height: 217px; background: var(--rule-grey);
  }

  .person { position: absolute; left: 445px; top: 130px; }
  .person__name { color: var(--brand-red); font-size: 30px; font-weight: 700; line-height: 1.1; }
  .person__role { color: var(--ink); font-size: 20px; font-weight: 500; margin-top: 2px; }

  .contact-list { list-style: none; margin-top: 20px; }
  .contact-list li {
    display: flex; align-items: center; height: 26px;
    font-size: 20px; color: var(--ink-soft);
  }
  .contact-list svg { width: 18px; height: 18px; margin-right: 12px; flex: none; }

  .front-rule {
    position: absolute; left: 0; right: 0; top: 432px;
    height: 3px; background: var(--rule-grey);
  }
  .office-band {
    position: absolute; left: 0; right: 0; bottom: 0; height: 34px;
    background: var(--brand-red); color: #fff;
    display: flex; align-items: center; justify-content: center;
    font-size: 19px;
  }
  .office-band .dot { margin: 0 6px; font-size: 14px; }

  /* Back */
  .group-brand {
    position: absolute; left: 0; right: 0; top: 142px;
    text-align: center; color: #fff; font-weight: 500; line-height: 1;
  }
  .group-brand__name { display: block; font-size: 86px; letter-spacing: 4px; }
  .group-brand__unit {
    display: block; font-size: 46px; text-align: right;
    width: 627px; margin: 6px 0 0 0;
  }

  .back-rule {
    position: absolute; left: 32px; right: 32px; top: 363px;
    height: 1px; background: rgba(255,255,255,0.85);
  }
  .agency-row {
    position: absolute; left: 32px; right: 32px; top: 385px;
    display: flex; justify-content: space-between;
  }
  .agency {
    color: #fff; font-weight: 500; text-align: right; line-height: 1;
    width: 160px;
  }
  .agency__name { display: block; font-size: 27px; letter-spacing: 0.5px; }
  .agency__unit { display: block; font-size: 17px; margin-top: 4px; }
  .agency--solo .agency__name { font-size: 21px; letter-spacing: 0; line-height: 1.15; }
</style>
</head>
<body>
<main class="stage">

  <section class="card card--front" aria-label="Card front">
    <div class="front-brand">
      <span class="front-brand__name">TELVANO</span>
      <span class="front-brand__unit">Media</span>
    </div>

    <div class="front-divider"></div>

    <div class="person">
      <h1 class="person__name">Lorenzo Varela</h1>
      <p class="person__role">Director</p>
      <ul class="contact-list">
        <li>
          <svg viewBox="0 0 24 24" aria-hidden="true"><path fill="var(--brand-red)" d="M6.6 10.8a15.1 15.1 0 0 0 6.6 6.6l2.2-2.2c.3-.3.7-.4 1-.2 1.1.4 2.3.6 3.6.6.6 0 1 .4 1 1V20c0 .6-.4 1-1 1A17 17 0 0 1 3 4c0-.6.4-1 1-1h3.5c.6 0 1 .4 1 1 0 1.3.2 2.5.6 3.6.1.3 0 .7-.2 1z"/></svg>
          910 555 214
        </li>
        <li>
          <svg viewBox="0 0 24 24" aria-hidden="true"><rect x="6" y="2" width="12" height="20" rx="2" fill="none" stroke="var(--brand-red)" stroke-width="2"/><circle cx="12" cy="18" r="1.2" fill="var(--brand-red)"/></svg>
          600 555 738
        </li>
        <li>
          <svg viewBox="0 0 24 24" aria-hidden="true"><rect x="2" y="5" width="20" height="14" fill="var(--brand-red)"/><path d="M2 5l10 8 10-8" fill="none" stroke="#fff" stroke-width="1.6"/></svg>
          lvarela@telvano.es
        </li>
        <li>
          <svg viewBox="0 0 24 24" aria-hidden="true"><rect x="3" y="3" width="18" height="18" fill="var(--brand-red)"/></svg>
          lorenzovarela
        </li>
        <li>
          <svg viewBox="0 0 24 24" aria-hidden="true"><circle cx="12" cy="12" r="10" fill="var(--brand-red)"/><ellipse cx="12" cy="12" rx="4" ry="10" fill="none" stroke="#fff" stroke-width="1.4"/><path d="M2 12h20" stroke="#fff" stroke-width="1.4"/></svg>
          telvano.es
        </li>
      </ul>
    </div>

    <div class="front-rule"></div>
    <footer class="office-band">
      Madrid <span class="dot">●</span> Barcelona <span class="dot">●</span> Valencia <span class="dot">●</span> Murcia
    </footer>
  </section>

  <section class="card card--back" aria-label="Card back">
    <div class="group-brand">
      <span class="group-brand__name">TELVANO</span>
      <span class="group-brand__unit">Grupo</span>
    </div>

    <div class="back-rule"></div>

    <div class="agency-row">
      <div class="agency"><span class="agency__name">TELVANO</span><span class="agency__unit">Digital</span></div>
      <div class="agency"><span class="agency__name">TELVANO</span><span class="agency__unit">Media</span></div>
      <div class="agency"><span class="agency__name">TELVANO</span><span class="agency__unit">Research</span></div>
      <div class="agency agency--solo"><span class="agency__name">DIFUNDE<br>ENPANTALLA</span></div>
    </div>
  </section>

</main>
</body>
</html>
```